International Chino Pant Manufacturer

We need modern packaging design for men's chino. All kinds of packaging designs are welcome.

The pant is folded and packaged in a poly bag. We require a label design for the brand name Tarvo. The main label will be attached by a string on the belt loop. the size of that label will 15cm in length and 5cm wide. This is the first label the customer see's when he picks up the garment. Therefore, we require an eye catching design for that. If required it could have certain information about the chino pant on the main label such as Comfort fit, Wrinkle-resistant, machine washable, luxury fabric. But, if you feel that adding the above information spoils the design of the label then it is not a must to include the above information. On the back of the label we like to include the information that this pant was manufactured in an Brena Summit certified green plant and hence the damage to the environment because of the plant is nill.

The second label label is attached on to the waist band and the purpose of that label is to include the size of the pant such 32x32. The size of that label is 8cm in length and 4cm in width. There is no design on the back on this label it has to be blank.

Industry/Entity Type

Manufacturer

```html
<!DOCTYPE html>
<html lang="en">
<head>
<meta charset="utf-8">
<title>Tarvo Chino Hang Tag – Back and Front</title>
<link href="https://fonts.googleapis.com/css2?family=Courier+Prime&family=Open+Sans:wght@700;800&display=swap" rel="stylesheet">
<style>
  :root {
    --stage-light: #ffffff;
    --stage-dark: #8e9092;
    --tan: #c9ac6c;
    --tan-deep: #a88a4e;
    --denim-shadow: #2a2418;
    --panel: #c99f52;
    --panel-stitch: #d9bd7e;
    --stitch: #e2cc94;
    --ink: #141210;
    --white: #ffffff;
  }
  * { margin: 0; padding: 0; box-sizing: border-box; }
  html, body { width: 1200px; height: 1000px; overflow: hidden; }
  body {
    position: relative;
    background: radial-gradient(ellipse at 50% 40%, var(--stage-light) 0%, #e4e5e6 35%, var(--stage-dark) 100%);
  }
  .tag {
    position: absolute;
    top: 42px;
    width: 305px;
    height: 893px;
    border-radius: 0 0 32px 32px;
    overflow: hidden;
  }
  .tag--back { left: 243px; }
  .tag--front { left: 651px; }
  .tag__texture {
    position: absolute; inset: 0;
    background:
      linear-gradient(160deg, transparent 0 20%, rgba(42,36,24,.55) 24%, transparent 30% 48%, rgba(42,36,24,.5) 54%, transparent 60% 78%, rgba(42,36,24,.6) 84%, transparent 90%),
      linear-gradient(200deg, var(--tan) 0%, var(--tan-deep) 50%, var(--tan) 100%);
  }
  .tag--front .tag__texture {
    background:
      linear-gradient(150deg, transparent 0 8%, rgba(42,36,24,.7) 12%, transparent 20% 42%, rgba(42,36,24,.75) 52%, rgba(42,36,24,.85) 70%, transparent 82%),
      linear-gradient(200deg, var(--tan) 0%, var(--tan-deep) 55%, var(--tan) 100%);
  }
  .tag__stitching { position: absolute; inset: 0; }
  .info-panel {
    position: absolute;
    left: 29px; top: 28px;
    width: 248px; height: 838px;
    background: var(--panel);
    border-radius: 4px 4px 22px 22px;
  }
  .brand-name {
    position: absolute;
    writing-mode: vertical-rl;
    font-family: "Open Sans", sans-serif;
    font-weight: 800;
    line-height: 1;
    text-transform: uppercase;
  }
  .tag--back .brand-name {
    left: 163px; top: 92px;
    font-size: 128px;
    letter-spacing: 2px;
    color: var(--ink);
  }
  .tag--front .brand-name {
    left: 88px; top: 128px;
    font-size: 136px;
    letter-spacing: -2px;
    color: var(--white);
  }
  .eco-statement {
    position: absolute;
    left: 78px; top: 84px;
    height: 770px;
    writing-mode: vertical-rl;
    font-family: "Courier Prime", monospace;
    font-size: 20px;
    letter-spacing: 3.8px;
    line-height: 20px;
    white-space: pre;
    color: var(--ink);
  }
  .feature-list {
    position: absolute;
    left: 90px; top: 606px;
    writing-mode: vertical-rl;
    list-style: none;
    font-family: "Open Sans", sans-serif;
    font-weight: 700;
    font-size: 24px;
    line-height: 35px;
    color: var(--white);
  }
</style>
</head>
<body>
  <section class="tag tag--back" aria-label="Hang tag back">
    <div class="tag__texture" role="img" aria-label="Close-up photograph of tan chino fabric with seams"></div>
    <div class="info-panel"></div>
    <svg class="tag__stitching" width="305" height="893" viewBox="0 0 305 893" aria-hidden="true">
      <path d="M33 32 H273 V846 Q273 862 257 862 H49 Q33 862 33 846 Z" fill="none" stroke="var(--panel-stitch)" stroke-width="2" stroke-dasharray="6 4"/>
    </svg>
    <p class="brand-name">Tarvo</p>
    <p class="eco-statement">this pant was manufactured in an Brena Summit
certified green plant and hence the damage to
the   environment because of the plant is nill.</p>
  </section>

  <section class="tag tag--front" aria-label="Hang tag front">
    <div class="tag__texture" role="img" aria-label="Close-up photograph of tan chino pocket and stitching"></div>
    <svg class="tag__stitching" width="305" height="893" viewBox="0 0 305 893" aria-hidden="true">
      <path d="M29 0 V835 Q29 863 57 863 H247 Q275 863 275 835 V0" fill="none" stroke="var(--stitch)" stroke-width="3" stroke-dasharray="10 6"/>
    </svg>
    <p class="brand-name">Tarvo</p>
    <ul class="feature-list">
      <li>Comfort fit</li>
      <li>Wrinkle-resistant</li>
      <li>machine washable</li>
      <li>luxury fabric</li>
    </ul>
  </section>
</body>
</html>
```